Veltrano.co - Polar Expeditions Specialists

We need a modern, visually striking business card for Veltrano.co, a company specialized in selling expedition cruises to the most remote regions on Earth, with a focus on the Arctic and Antarctica. The design should instantly communicate that the cardholder is an expert in polar travel. Use clean, premium aesthetics with cool tones like icy blue and white, possibly incorporating polar imagery (ice, glaciers, penguins, etc.)

Attached the logo

Contact Information for Business Card

Feels high-end and trustworthy.. Visually memorable — encourages people to keep it

Colors
0054AA
0677BA
7BADD7
CADEEF
E8F1F8

Requirements
Must have
• ice, glaciers, penguins, montains
Nice to have
• modern, transparente,

```html
<!DOCTYPE html>
<html lang="en">
<head>
<meta charset="utf-8">
<title>Veltrano.co – Business Card</title>
<link rel="stylesheet" href="https://fonts.googleapis.com/css2?family=Poppins:wght@600;800&family=Montserrat:wght@400;500&display=swap">
<style>
  :root {
    --deep-blue: #0054AA;
    --brand-blue: #2F78BD;
    --mid-blue: #0677BA;
    --soft-blue: #7BADD7;
    --pale-blue: #CADEEF;
    --ice: #E8F1F8;
    --ink: #3a3f47;
    --stage: #e4e6e9;
    --white: #ffffff;
  }
  * { box-sizing: border-box; margin: 0; padding: 0; }
  html, body { width: 1200px; height: 900px; overflow: hidden; }
  body {
    background: var(--stage);
    display: flex;
    flex-direction: column;
    align-items: center;
    justify-content: center;
    gap: 36px;
    font-family: "Montserrat", sans-serif;
  }
  .card {
    position: relative;
    width: 700px;
    height: 400px;
    border-radius: 26px;
    overflow: hidden;
    box-shadow: 0 10px 28px rgba(0, 0, 0, 0.18);
  }

  /* Front */
  .card-front { background: #5b93c9; }
  .front-photo {
    position: absolute; inset: 0;
    background:
      radial-gradient(ellipse 38% 48% at 58% 48%, rgba(202, 222, 239, 0.55), rgba(123, 173, 215, 0) 70%),
      linear-gradient(180deg, #5a92c8 0%, #5d95cb 55%, #7aa9d6 100%);
  }
  .front-brand {
    position: absolute;
    left: 240px; top: 150px;
    color: var(--white);
  }
  .brand-name {
    font-family: "Poppins", sans-serif;
    font-weight: 800;
    font-size: 68px;
    line-height: 1;
    letter-spacing: 1px;
  }
  .brand-tagline {
    font-family: "Poppins", sans-serif;
    font-weight: 600;
    font-size: 18px;
    margin-top: 8px;
    margin-left: 4px;
  }
  .brand-dot {
    display: inline-block;
    width: 16px; height: 16px;
    border-radius: 50%;
    margin-right: 12px;
    vertical-align: middle;
  }
  .front-brand .brand-dot { background: var(--white); }

  /* Back */
  .card-back { background: var(--white); }
  .back-tab {
    position: absolute;
    right: 0; top: 30px;
    width: 18px; height: 48px;
    background: var(--brand-blue);
  }
  .holder {
    position: absolute;
    right: 34px; top: 34px;
    text-align: right;
  }
  .holder-name {
    font-family: "Poppins", sans-serif;
    font-weight: 800;
    font-size: 30px;
    color: var(--brand-blue);
    letter-spacing: 1.5px;
    line-height: 1.05;
  }
  .holder-role {
    font-size: 18px;
    color: var(--ink);
    margin-top: 2px;
  }
  .back-brand {
    position: absolute;
    left: 52px; top: 148px;
    color: var(--brand-blue);
  }
  .back-brand .brand-name { font-size: 56px; }
  .back-brand .brand-tagline { font-size: 15px; }
  .back-brand .brand-dot { background: var(--brand-blue); width: 14px; height: 14px; }

  .address {
    position: absolute;
    left: 56px; top: 270px;
    font-size: 16px;
    line-height: 1.3;
    color: var(--ink);
  }
  .contacts {
    position: absolute;
    left: 56px; top: 320px;
    list-style: none;
    font-size: 16px;
    line-height: 1.35;
    color: var(--ink);
  }
  .contacts li { display: flex; align-items: center; gap: 10px; }
  .contacts svg { width: 14px; height: 14px; fill: var(--brand-blue); flex: none; }
</style>
</head>
<body>

  <section class="card card-front" aria-label="Card front">
    <div class="front-photo" role="img" aria-label="Photograph of a polar bear walking on snow and ice, tinted blue"></div>
    <div class="front-brand">
      <div class="brand-name"><span class="brand-dot"></span>Veltrano.co</div>
      <div class="brand-tagline">Polar Expeditions Specialists</div>
    </div>
  </section>

  <section class="card card-back" aria-label="Card back">
    <div class="back-tab"></div>
    <div class="holder">
      <div class="holder-name">DANIEL MOREAU</div>
      <div class="holder-role">CEO / Founder</div>
    </div>
    <div class="back-brand">
      <div class="brand-name"><span class="brand-dot"></span>Veltrano.co</div>
      <div class="brand-tagline">Polar Expeditions Specialists</div>
    </div>
    <p class="address">P.O. Box 3120 Harbour Lane<br>Northvale NV 4417</p>
    <ul class="contacts">
      <li>
        <svg viewBox="0 0 24 24" aria-hidden="true"><path d="M6.6 10.8a15.1 15.1 0 0 0 6.6 6.6l2.2-2.2a1 1 0 0 1 1-.25 11.4 11.4 0 0 0 3.6.57 1 1 0 0 1 1 1V20a1 1 0 0 1-1 1A17 17 0 0 1 3 4a1 1 0 0 1 1-1h3.5a1 1 0 0 1 1 1c0 1.25.2 2.45.57 3.6a1 1 0 0 1-.25 1z"/></svg>
        +43 512 48 90 317
      </li>
      <li>
        <svg viewBox="0 0 24 24" aria-hidden="true"><path d="M3 5h18a1 1 0 0 1 1 1v12a1 1 0 0 1-1 1H3a1 1 0 0 1-1-1V6a1 1 0 0 1 1-1zm9 7 8-5H4z"/></svg>
        daniel.moreau@veltrano.co
      </li>
      <li>
        <svg viewBox="0 0 24 24" aria-hidden="true"><circle cx="12" cy="12" r="10"/></svg>
        www.veltrano.co
      </li>
    </ul>
  </section>

</body>
</html>
```